Brightway Carpet and Tile cleaning Business card Design

I need a design that has the same feel as my van.
i would also like a prominent "Review us on facebook" somewhere, but not that it makes it look silly.
I would like the card to have a little bit of grey or black in the design as well.

It will need contact details
phone: 0455 817264
email: rkbrightwayclean@mailbox-example.com
website: www.brightwaycarpetandtilecleaning-example.com.au
facebook: /brightwaycarpetandtilecleaning

Industry/Entity Type

Business

Contact Information for Business Card

Phone number 0455817264
Email rkbrightwayclean@mailbox-example.com
Website www.brightwaycarpetandtilecleaning-example.com.au
Facebook/brightwaycarpetandtilecleaning

Colors
000000

Requirements
Must have
• Same feel as my van
• I want the card to stand out from the crowd
Nice to have
• Maybe include a tiny bit of a third colour? Grey's,blacks, orange?

```html
<!DOCTYPE html>
<html lang="en">
<head>
<meta charset="utf-8">
<title>Brightway Carpet and Tile cleaning – Business Card</title>
<link rel="stylesheet" href="https://fonts.googleapis.com/css2?family=PT+Sans:wght@400;700&display=swap">
<style>
  :root {
    --page-bg: #e9e7e3;
    --card-black: #1c1c1d;
    --card-black-light: #2a2a2c;
    --text-white: #f4f4f4;
    --stripe-white: #eceeef;
    --stripe-blue: #0ca9dc;
    --stripe-green: #79bd3a;
    --icon-social: #4a4fa0;
    --icon-phone: #1aa6dc;
    --icon-mail: #3a3a3c;
    --icon-web: #4cae48;
  }
  html, body {
    margin: 0;
    width: 1200px;
    height: 1023px;
    overflow: hidden;
    background: var(--page-bg);
  }
  .business-card {
    position: absolute;
    left: 100px;
    top: 225px;
    width: 1000px;
    height: 572px;
    background: linear-gradient(135deg, var(--card-black-light) 0%, var(--card-black) 45%, var(--card-black) 100%);
    box-shadow: 0 12px 30px rgba(0,0,0,0.25);
    overflow: hidden;
    font-family: "PT Sans", "Myriad Pro", sans-serif;
    color: var(--text-white);
  }
  .brand-stripe {
    position: absolute;
    right: 0;
    top: 0;
    width: 42px;
    height: 100%;
    display: flex;
    flex-direction: column;
  }
  .brand-stripe span { flex: 1; }
  .stripe-white { background: var(--stripe-white); }
  .stripe-blue { background: var(--stripe-blue); }
  .stripe-green { background: var(--stripe-green); }
  .review-headline {
    position: absolute;
    left: 150px;
    top: 118px;
    display: flex;
    align-items: center;
    gap: 26px;
    font-size: 46px;
    letter-spacing: 0.5px;
    white-space: nowrap;
  }
  .review-headline .ring {
    width: 54px;
    height: 54px;
    border: 4px solid var(--text-white);
    border-radius: 50%;
    box-sizing: border-box;
  }
  .review-headline strong { font-weight: 700; }
  .contact-list {
    position: absolute;
    left: 150px;
    top: 222px;
    margin: 0;
    padding: 0;
    list-style: none;
  }
  .contact-item {
    display: flex;
    align-items: center;
    gap: 26px;
    height: 54px;
    margin-bottom: 20px;
    font-size: 29px;
    white-space: nowrap;
  }
  .contact-icon {
    width: 54px;
    height: 54px;
    flex: none;
    border-radius: 50%;
    border: 3px solid #e8e8e8;
    box-sizing: border-box;
    display: flex;
    align-items: center;
    justify-content: center;
  }
  .icon-social { background: var(--icon-social); }
  .icon-phone { background: var(--icon-phone); }
  .icon-mail { background: var(--icon-mail); }
  .icon-web { background: var(--icon-web); }
</style>
</head>
<body>
  <div class="business-card">
    <div class="brand-stripe">
      <span class="stripe-white"></span>
      <span class="stripe-blue"></span>
      <span class="stripe-green"></span>
    </div>

    <div class="review-headline">
      <span class="ring"></span>
      <span>Review Us On <strong>Socialspot!</strong></span>
    </div>

    <ul class="contact-list">
      <li class="contact-item">
        <span class="contact-icon icon-social"></span>
        <span>brightwaycarpetandtilecleaning</span>
      </li>
      <li class="contact-item">
        <span class="contact-icon icon-phone">
          <svg width="26" height="26" viewBox="0 0 24 24" aria-hidden="true">
            <path fill="#fff" d="M6.6 10.8a15.1 15.1 0 0 0 6.6 6.6l2.2-2.2c.3-.3.7-.4 1-.2 1.1.4 2.3.6 3.6.6.6 0 1 .4 1 1V20c0 .6-.4 1-1 1A17 17 0 0 1 3 4c0-.6.4-1 1-1h3.5c.6 0 1 .4 1 1 0 1.3.2 2.5.6 3.6.1.3 0 .7-.2 1z"/>
          </svg>
        </span>
        <span>0455 817264</span>
      </li>
      <li class="contact-item">
        <span class="contact-icon icon-mail">
          <svg width="26" height="20" viewBox="0 0 26 20" aria-hidden="true">
            <rect x="1" y="1" width="24" height="18" fill="#fff"/>
            <path d="M1 1 L13 11 L25 1" fill="none" stroke="#3a3a3c" stroke-width="2"/>
          </svg>
        </span>
        <span>rkbrightwayclean@mailbox-example.com</span>
      </li>
      <li class="contact-item">
        <span class="contact-icon icon-web">
          <svg width="26" height="26" viewBox="0 0 24 24" aria-hidden="true">
            <g fill="none" stroke="#fff" stroke-width="2.6" stroke-linecap="round">
              <path d="M10 14a4 4 0 0 0 5.7 0l3-3a4 4 0 0 0-5.7-5.7l-1 1"/>
              <path d="M14 10a4 4 0 0 0-5.7 0l-3 3a4 4 0 0 0 5.7 5.7l1-1"/>
            </g>
          </svg>
        </span>
        <span>www.brightwaycarpetandtilecleaning-example.com.au</span>
      </li>
    </ul>
  </div>
</body>
</html>
```